Silver Tsunami E-Blast to Customers

We are looking for a fresh e-blast design that is in line with company branding (pvmholdco.com). Please use the attached logo and include the copy below. The images below are inspiration. We’d like the image of a senior (older) woman surfer on a GINORMOUS wave crouched low.
Specs:
600px w x 1500px h
Copy:
(big, bold header) Catch a Swell via PVM's Funding Toolkit!
The Silver Tsunami is surging ashore! Smart operators aren't bracing for impact, they're grabbing their boards and riding the wave of opportunity.
PVM has a full quiver of flexible financing solutions to help you stay afloat, whether you're looking to acquire, build, or refinance.
Paddle out alongside PVM!
Attending ORB in San Diego?
Let's connect.
Our financing solutions include:
Acquisitions
Construction
Refinancing
Recapitalizations
Structured Leases
Bridge
Mezzanine
Unitranche
NNN Lease
Preferred Equity

```html
<!DOCTYPE html>
<html lang="en">
<head>
<meta charset="utf-8">
<title>PVM Silver Tsunami E-Blast</title>
<link rel="stylesheet" href="https://fonts.googleapis.com/css2?family=Oswald:wght@500&family=Montserrat:wght@400;500;700;900&display=swap">
<style>
  :root {
    --stage: #2a2829;
    --navy: #0c2f8f;
    --ink: #132c8a;
    --bright: #1470d0;
    --sky: #6cc6ec;
    --royal: #1274d6;
    --white: #ffffff;
    --teal-deep: #0c4f5c;
    --teal-mid: #1b8c9c;
    --teal-light: #7fd6e2;
  }
  * { box-sizing: border-box; margin: 0; padding: 0; }
  html, body { width: 1200px; height: 1200px; overflow: hidden; }
  body { background: var(--stage); position: relative; font-family: "Montserrat", sans-serif; }

  .eblast {
    position: absolute; left: 389px; top: 70px; width: 424px; height: 1061px;
    background: var(--white); overflow: hidden;
    box-shadow: 0 6px 24px rgba(0,0,0,.45);
  }

  .hero {
    position: absolute; left: 0; top: 0; width: 424px; height: 466px;
    background:
      radial-gradient(ellipse at 78% 52%, var(--teal-light) 0%, rgba(127,214,226,0) 38%),
      linear-gradient(160deg, var(--teal-mid) 0%, var(--teal-deep) 55%, #0a4552 100%);
  }
  .brand {
    position: absolute; left: 22px; top: 46px; display: flex; align-items: center; gap: 10px;
  }
  .brand-square { width: 30px; height: 30px; background: var(--white); }
  .brand-name {
    font-family: "Montserrat", sans-serif; font-weight: 700; font-size: 40px;
    color: var(--white); letter-spacing: 1px; line-height: 1;
  }
  .headline {
    position: absolute; left: 21px; top: 196px; width: 390px;
    font-family: "Oswald", sans-serif; font-weight: 500; font-size: 66px;
    line-height: 65px; color: var(--white); letter-spacing: -0.5px;
  }

  .wave-band {
    position: absolute; left: 0; top: 466px; width: 424px; height: 11px;
    background: linear-gradient(90deg, var(--royal) 0%, #8fd0f2 40%, #e8f6fd 55%, #8fd0f2 75%, var(--royal) 100%);
  }

  .body-copy { position: absolute; left: 21px; width: 340px; color: var(--ink); }
  .lead {
    top: 486px; font-weight: 700; font-size: 18.5px; width: 390px; white-space: nowrap;
  }
  .para { font-weight: 500; font-size: 14.6px; line-height: 21px; }
  .para-one { top: 522px; }
  .para-two { top: 621px; }
  .divider {
    position: absolute; left: 21px; top: 600px; width: 63px; height: 6px; background: var(--navy);
  }
  .cta {
    position: absolute; left: 21px; top: 718px; font-weight: 900; font-size: 21px;
    color: var(--bright); white-space: nowrap;
  }

  .event {
    position: absolute; left: 21px; top: 762px; width: 382px; height: 82px; display: flex;
  }
  .event-text { width: 240px; background: var(--sky); padding: 13px 0 0 7px; color: var(--navy); }
  .event-ask { font-weight: 400; font-size: 15.5px; color: var(--white); }
  .event-connect { font-weight: 900; font-size: 27px; margin-top: 4px; letter-spacing: -0.3px; }
  .event-badge {
    flex: 1; background: var(--royal); display: flex; align-items: center; justify-content: center;
    font-weight: 900; font-size: 48px; color: var(--white); letter-spacing: 1px;
  }

  .list-title {
    position: absolute; left: 21px; top: 856px; font-weight: 700; font-size: 19px; color: var(--ink);
  }
  .solutions {
    position: absolute; left: 21px; top: 892px; width: 390px; list-style: none;
    display: grid; grid-template-columns: 230px 160px; grid-auto-flow: column;
    grid-template-rows: repeat(5, 25px);
  }
  .solutions li {
    display: flex; align-items: center; gap: 11px; font-weight: 700; font-size: 15px; color: var(--ink);
  }
  .solutions svg { width: 11px; height: 11px; flex: none; }

  .footer {
    position: absolute; left: 0; top: 1025px; width: 424px; height: 36px; background: var(--navy);
    color: var(--white); font-weight: 700; font-size: 14px; display: flex; align-items: center; justify-content: center;
  }
</style>
</head>
<body>
  <main class="eblast">
    <section class="hero" role="img" aria-label="Photo of an older woman surfer crouched low on a pink board inside a giant teal wave">
      <div class="brand">
        <span class="brand-square"></span>
        <span class="brand-name">PVM</span>
      </div>
      <h1 class="headline">Catch a Swell via PVM's Funding Toolkit!</h1>
    </section>
    <div class="wave-band"></div>

    <p class="body-copy lead">The Silver Tsunami is surging ashore!</p>
    <p class="body-copy para para-one">Smart operators aren't bracing for impact, they're grabbing their boards and riding the wave of opportunity.</p>
    <div class="divider"></div>
    <p class="body-copy para para-two">PVM has a full quiver of flexible financing solutions to help you stay afloat, whether you're looking to acquire, build, or refinance.</p>
    <p class="cta">Paddle out alongside PVM!</p>

    <section class="event">
      <div class="event-text">
        <p class="event-ask">Attending ORB in San Diego?</p>
        <p class="event-connect">Let's connect.</p>
      </div>
      <div class="event-badge">ORB</div>
    </section>

    <h2 class="list-title">Our financing solutions include:</h2>
    <ul class="solutions">
      <li><svg viewBox="0 0 12 12"><circle cx="6" cy="6" r="5" fill="none" stroke="#1470d0" stroke-width="1.2"/><path d="M3.6 6.2l1.7 1.6 3.2-3.4" fill="none" stroke="#1470d0" stroke-width="1.2"/></svg>Acquisitions</li>
      <li><svg viewBox="0 0 12 12"><circle cx="6" cy="6" r="5" fill="none" stroke="#1470d0" stroke-width="1.2"/><path d="M3.6 6.2l1.7 1.6 3.2-3.4" fill="none" stroke="#1470d0" stroke-width="1.2"/></svg>Construction</li>
      <li><svg viewBox="0 0 12 12"><circle cx="6" cy="6" r="5" fill="none" stroke="#1470d0" stroke-width="1.2"/><path d="M3.6 6.2l1.7 1.6 3.2-3.4" fill="none" stroke="#1470d0" stroke-width="1.2"/></svg>Refinancing</li>
      <li><svg viewBox="0 0 12 12"><circle cx="6" cy="6" r="5" fill="none" stroke="#1470d0" stroke-width="1.2"/><path d="M3.6 6.2l1.7 1.6 3.2-3.4" fill="none" stroke="#1470d0" stroke-width="1.2"/></svg>Recapitalizations</li>
      <li><svg viewBox="0 0 12 12"><circle cx="6" cy="6" r="5" fill="none" stroke="#1470d0" stroke-width="1.2"/><path d="M3.6 6.2l1.7 1.6 3.2-3.4" fill="none" stroke="#1470d0" stroke-width="1.2"/></svg>Structured Leases</li>
      <li><svg viewBox="0 0 12 12"><circle cx="6" cy="6" r="5" fill="none" stroke="#1470d0" stroke-width="1.2"/><path d="M3.6 6.2l1.7 1.6 3.2-3.4" fill="none" stroke="#1470d0" stroke-width="1.2"/></svg>Bridge</li>
      <li><svg viewBox="0 0 12 12"><circle cx="6" cy="6" r="5" fill="none" stroke="#1470d0" stroke-width="1.2"/><path d="M3.6 6.2l1.7 1.6 3.2-3.4" fill="none" stroke="#1470d0" stroke-width="1.2"/></svg>Mezzanine</li>
      <li><svg viewBox="0 0 12 12"><circle cx="6" cy="6" r="5" fill="none" stroke="#1470d0" stroke-width="1.2"/><path d="M3.6 6.2l1.7 1.6 3.2-3.4" fill="none" stroke="#1470d0" stroke-width="1.2"/></svg>Unitranche</li>
      <li><svg viewBox="0 0 12 12"><circle cx="6" cy="6" r="5" fill="none" stroke="#1470d0" stroke-width="1.2"/><path d="M3.6 6.2l1.7 1.6 3.2-3.4" fill="none" stroke="#1470d0" stroke-width="1.2"/></svg>NNN Lease</li>
      <li><svg viewBox="0 0 12 12"><circle cx="6" cy="6" r="5" fill="none" stroke="#1470d0" stroke-width="1.2"/><path d="M3.6 6.2l1.7 1.6 3.2-3.4" fill="none" stroke="#1470d0" stroke-width="1.2"/></svg>Preferred Equity</li>
    </ul>

    <footer class="footer">www.pvmholdco.com</footer>
  </main>
</body>
</html>
```